Packaging for educational products for special needs kids - Drawer (pull-out) box

1. Modern, minimalist but attractive packaging for educational products for kids.
2. Approx size 24 x 15.5 x 2 cm.
3. Please refer to the sample packaging image for the kind of information that will be placed on the box. But the new designed box will be white.
4. The background on the sample images of a boy and a girl is used on all the cards so you can refer to this colour to be used in your designs.

Font styles to use
Sans Serif

Colors
87cfc6
cfeae6
f04a50
faa54b
fbee3d
abd036
00a990

```html
<!DOCTYPE html>
<html lang="en">
<head>
<meta charset="utf-8">
<title>Visual Learning Support – Drawer Box Lids</title>
<link rel="stylesheet" href="https://fonts.googleapis.com/css2?family=Baloo+2:wght@600;800&display=swap">
<style>
  :root {
    --stage: #8e8e8e;
    --board: #f4f4f3;
    --girl: #e7509b;
    --boy: #35a6dc;
    --boy-tag: #e8262d;
    --brand: #2a3f9c;
    --calendar: #6c8a96;
    --calendar-page: #eef2f4;
    --girl-art: #e9a0b5;
    --boy-art: #e3c25a;
  }
  * { box-sizing: border-box; margin: 0; padding: 0; }
  html, body { width: 1185px; height: 1200px; overflow: hidden; }
  body {
    background: var(--stage);
    font-family: "Baloo 2", sans-serif;
    position: relative;
  }
  .lid {
    position: absolute;
    left: 210px;
    width: 717px;
    height: 452px;
    background: var(--board);
    --accent: var(--girl);
    --tag: var(--girl);
    --art: var(--girl-art);
  }
  .lid--girl { top: 52px; }
  .lid--boy { top: 684px; left: 212px; --accent: var(--boy); --tag: var(--boy-tag); --art: var(--boy-art); }

  .brand {
    position: absolute;
    top: 62px; left: 0; width: 100%;
    display: flex; justify-content: center; align-items: center; gap: 6px;
    font-weight: 800; font-size: 22px; color: var(--brand); line-height: 1;
  }
  .brand__dot { width: 12px; height: 12px; border-radius: 50%; background: var(--brand); }

  .character {
    position: absolute; left: 404px; top: 134px; width: 90px; height: 104px;
    border-radius: 45px 45px 8px 8px;
    background: linear-gradient(180deg, #9a5a3a 0%, var(--art) 100%);
  }
  .calendar {
    position: absolute; left: 222px; top: 200px; width: 142px; height: 140px;
    border-radius: 14px;
    background: linear-gradient(160deg, var(--calendar-page) 0%, var(--calendar) 100%);
  }

  .title {
    position: absolute; left: 366px; top: 240px; width: 174px; height: 86px;
    border-top: 2px dotted var(--accent);
    border-bottom: 2px dotted var(--accent);
    padding-top: 2px;
    color: var(--accent); text-align: center; white-space: nowrap;
  }
  .title__main { display: block; font-weight: 800; font-size: 52px; line-height: 1; letter-spacing: -0.5px; }
  .title__sub { display: block; font-weight: 800; font-size: 17.5px; line-height: 1.1; margin-top: 2px; }

  .package-tag {
    position: absolute; left: 24px; top: 405px;
    display: flex; height: 20px; border: 1.5px solid var(--tag);
    font-weight: 800; font-size: 12px; line-height: 17px; white-space: nowrap;
  }
  .package-tag__label { padding: 0 4px; color: var(--tag); background: #fff; }
  .package-tag__value { padding: 0 6px; color: #fff; background: var(--tag); }

  .care-icons {
    position: absolute; right: 38px; top: 406px;
    display: flex; gap: 6px;
  }
  .care-icons svg { width: 18px; height: 18px; }
</style>
</head>
<body>

<section class="lid lid--girl">
  <div class="brand"><span class="brand__dot"></span>Bright Sprouts</div>
  <div class="character" role="img" aria-label="Illustration of a smiling girl in a pink top"></div>
  <div class="calendar" role="img" aria-label="Desk calendar illustration in grey-blue tones"></div>
  <h2 class="title"><span class="title__main">VISUAL</span><span class="title__sub">LEARNING SUPPORT</span></h2>
  <div class="package-tag"><span class="package-tag__label">Package For</span><span class="package-tag__value">GIRL</span></div>
  <div class="care-icons" aria-label="Handling icons">
    <svg viewBox="0 0 20 20"><circle cx="10" cy="10" r="9" fill="none" stroke="var(--girl)" stroke-width="1.4"/><path d="M10 4 C13 8 14 10 14 12 A4 4 0 0 1 6 12 C6 10 7 8 10 4Z" fill="var(--girl)"/></svg>
    <svg viewBox="0 0 20 20"><circle cx="10" cy="10" r="9" fill="none" stroke="var(--girl)" stroke-width="1.4"/><path d="M4 10 A6 5 0 0 1 16 10Z" fill="var(--girl)"/><path d="M10 10 V15 A1.5 1.5 0 0 1 7 15" fill="none" stroke="var(--girl)" stroke-width="1.3"/></svg>
    <svg viewBox="0 0 20 20"><circle cx="10" cy="10" r="9" fill="none" stroke="var(--girl)" stroke-width="1.4"/><path d="M10 5 L14 12 H6Z" fill="none" stroke="var(--girl)" stroke-width="1.6"/></svg>
    <svg viewBox="0 0 20 20"><circle cx="10" cy="10" r="9" fill="none" stroke="var(--girl)" stroke-width="1.4"/><path d="M10 4 C14 8 14 11 13 13 A3.5 3.5 0 0 1 7 13 C6 11 7 9 8 8 C8 10 9 10 10 4Z" fill="var(--girl)"/></svg>
    <svg viewBox="0 0 20 20"><circle cx="10" cy="10" r="9" fill="none" stroke="var(--girl)" stroke-width="1.4"/><path d="M7.5 15 V6 M5.5 8 L7.5 5.5 L9.5 8 M12.5 15 V6 M10.5 8 L12.5 5.5 L14.5 8" fill="none" stroke="var(--girl)" stroke-width="1.4"/></svg>
  </div>
</section>

<section class="lid lid--boy">
  <div class="brand"><span class="brand__dot"></span>Bright Sprouts</div>
  <div class="character" role="img" aria-label="Illustration of a smiling boy in a yellow shirt"></div>
  <div class="calendar" role="img" aria-label="Desk calendar illustration in grey-blue tones"></div>
  <h2 class="title"><span class="title__main">VISUAL</span><span class="title__sub">LEARNING SUPPORT</span></h2>
  <div class="package-tag"><span class="package-tag__label">Package For</span><span class="package-tag__value">BOYS</span></div>
  <div class="care-icons" aria-label="Handling icons">
    <svg viewBox="0 0 20 20"><circle cx="10" cy="10" r="9" fill="none" stroke="var(--boy-tag)" stroke-width="1.4"/><path d="M10 4 C13 8 14 10 14 12 A4 4 0 0 1 6 12 C6 10 7 8 10 4Z" fill="var(--boy-tag)"/></svg>
    <svg viewBox="0 0 20 20"><circle cx="10" cy="10" r="9" fill="none" stroke="var(--boy-tag)" stroke-width="1.4"/><path d="M4 10 A6 5 0 0 1 16 10Z" fill="var(--boy-tag)"/><path d="M10 10 V15 A1.5 1.5 0 0 1 7 15" fill="none" stroke="var(--boy-tag)" stroke-width="1.3"/></svg>
    <svg viewBox="0 0 20 20"><circle cx="10" cy="10" r="9" fill="none" stroke="var(--boy-tag)" stroke-width="1.4"/><path d="M10 5 L14 12 H6Z" fill="none" stroke="var(--boy-tag)" stroke-width="1.6"/></svg>
    <svg viewBox="0 0 20 20"><circle cx="10" cy="10" r="9" fill="none" stroke="var(--boy-tag)" stroke-width="1.4"/><path d="M10 4 C14 8 14 11 13 13 A3.5 3.5 0 0 1 7 13 C6 11 7 9 8 8 C8 10 9 10 10 4Z" fill="var(--boy-tag)"/></svg>
    <svg viewBox="0 0 20 20"><circle cx="10" cy="10" r="9" fill="none" stroke="var(--boy-tag)" stroke-width="1.4"/><path d="M7.5 15 V6 M5.5 8 L7.5 5.5 L9.5 8 M12.5 15 V6 M10.5 8 L12.5 5.5 L14.5 8" fill="none" stroke="var(--boy-tag)" stroke-width="1.4"/></svg>
  </div>
</section>

</body>
</html>
```